Web design for financial services

A modern web design of financial services (brokerage firm)
Req.s and technology tags :
- Very mobile friendly.
- One paged with some inner pages.
- Animated sticky header .
- Member login area for e-trade.
- Support RTL language.
- HTML & CSS.

The logo will be Home link
• MPTR :
WHO WE ARE
Content :
i) Board of Directors
ii) Mission Statement
iii) Corporate Values
iv) Regulations
• Financial Services :
WHAT WE DO
Content:
i) Electronic trading
ii) Trading desk
iii) Institutional
iv) Investors Education
• News
• Market Tools
• Forms---- opens new page
• Careers---- opens new page
• Contact Us----opens new page

The website is :
http://www.mptr-doha-example.com/

The logo need some changes to be more modern and impressively , but with keeping same structure .

Some related websites :
https://www.lv-bourse.example/

financial market

Financial Service

Coded - Design and coding required

2 page

• same fonts of http://www.kwdholdings.example/

• - Very mobile friendly.
• - One paged with some inner pages.
• - Animated sticky header .
• - Member login area for e-trade.
• - Support RTL language.
• - HTML & CSS.
• Slider , some Qatari theme,
• i like the video inside the home page
• ex :http://www.kwdholdings.example/

```html
<!DOCTYPE html>
<html lang="en">
<head>
<meta charset="utf-8">
<title>MPTR — Financial Services</title>
<link href="https://fonts.googleapis.com/css2?family=Open+Sans:wght@300;400;600&family=Oswald:wght@400&display=swap" rel="stylesheet">
<style>
:root{
  --accent:#9e1f24;
  --ink:#2b2b2b;
  --body:#555;
  --muted:#888;
  --line:#ddd;
  --band:#f2f2f2;
  --band-dark:#e8e8e8;
  --partner:#d4d4d4;
  --white:#fff;
}
*{box-sizing:border-box;margin:0;padding:0}
html,body{width:1200px;height:2812px;overflow:hidden;background:var(--white)}
body{font-family:"Open Sans",Arial,sans-serif;color:var(--body);position:relative}
a{text-decoration:none;color:inherit}
.abs{position:absolute}

/* header */
.site-header{position:absolute;left:0;top:0;width:1200px;height:131px;background:var(--white)}
.brand{position:absolute;left:90px;top:40px;display:flex;align-items:center;gap:10px;text-decoration:none}
.brand-mark{width:22px;height:22px;border-radius:50%;background:var(--accent)}
.brand-name{font-size:28px;font-weight:600;color:var(--accent);letter-spacing:1px;line-height:1}
.main-nav a{position:absolute;top:52px;font-size:16px;color:var(--ink);line-height:24px}
.main-nav .is-active{border:1px solid var(--accent);color:var(--accent);border-radius:14px;padding:0 18px;top:50px}
.main-nav .login{background:var(--accent);color:var(--white);border-radius:18px;padding:6px 22px;top:45px}
.lang{position:absolute;left:1002px;top:50px;display:flex;align-items:center;gap:6px;font-size:15px;color:var(--ink)}
.lang-dot{width:22px;height:22px;border-radius:50%;background:linear-gradient(#b8c4dc,#d7a0a6)}

/* hero */
.hero{position:absolute;left:0;top:131px;width:1200px;height:503px;
  background:linear-gradient(170deg,#4c5f70 0%,#6e7c86 40%,#3f6f86 70%,#2c5872 100%)}
.hero-copy{position:absolute;left:0;right:0;top:165px;text-align:center;color:var(--white)}
.hero-title{font-size:84px;font-weight:300;line-height:1}
.hero-sub{font-family:"Oswald",Arial,sans-serif;font-size:40px;margin-top:2px}
.hero-arrow{position:absolute;top:262px;width:14px;height:14px}

/* sections */
.section-title{font-size:28px;font-weight:400;color:var(--ink);letter-spacing:.5px}
.copy{font-size:13.5px;line-height:22px;color:var(--body);text-align:justify}
.btn-outline{display:inline-block;border:1.5px solid var(--accent);color:var(--accent);border-radius:18px;
  font-size:12px;padding:7px 14px;margin-top:20px}
.placeholder{border-radius:4px}

.who{position:absolute;left:0;top:634px;width:1200px;height:482px}
.what{position:absolute;left:0;top:1116px;width:1200px;height:395px;background:var(--band)}

/* news */
.news-title{position:absolute;left:0;right:0;top:1562px;text-align:center}
.news-card{position:absolute;top:1625px;width:311px;text-align:center}
.news-card .photo{height:199px}
.news-card h3{font-size:17px;font-weight:400;color:var(--ink);margin-top:18px}
.news-card time{display:block;font-size:16px;color:var(--body)}

.partners{position:absolute;left:112px;top:1982px;width:980px;display:flex;justify-content:space-between;align-items:center}
.partner{width:100px;height:30px;border-radius:3px;background:var(--partner)}

/* market */
.market{position:absolute;left:0;top:2075px;width:1200px;height:460px;background:var(--band-dark)}
.market .section-title{position:absolute;left:0;right:0;top:33px;text-align:center}
.tool-card{position:absolute;top:96px;width:329px;height:317px;background:var(--white);
  box-shadow:0 1px 4px rgba(0,0,0,.15);padding:22px 20px}
.tool-card h3{font-size:21px;font-weight:400;color:var(--ink);text-align:center;padding-bottom:10px;border-bottom:1px solid var(--line)}
.tool-card ul{list-style:none;margin-top:18px;padding-left:20px}
.tool-card li{font-size:14px;color:var(--ink);line-height:31px;display:flex;align-items:center;gap:10px}
.tool-card li svg{flex:none}

/* footer */
.site-footer{position:absolute;left:0;top:2535px;width:1200px;height:277px}
.foot-brand{position:absolute;left:94px;top:76px;display:flex;align-items:center;gap:8px;text-decoration:none}
.foot-col{position:absolute;top:54px}
.foot-col h4{font-size:15px;font-weight:400;color:var(--ink);margin-bottom:16px}
.foot-col p{font-size:12px;line-height:21px;color:var(--muted)}
.mail-form{display:flex;margin-top:12px}
.mail-form span{width:150px;height:30px;border:1px solid var(--line);font-size:12px;color:var(--muted);padding:6px 8px}
.mail-form b{height:30px;background:var(--accent);color:var(--white);font-weight:400;font-size:12px;padding:6px 10px}
.socials{display:flex;gap:12px}
.socials span{width:26px;height:26px;border-radius:3px;background:#6b6b6b}
.foot-rule{position:absolute;left:88px;right:88px;top:214px;border-top:1px solid var(--line)}
.copyright{position:absolute;left:0;right:0;top:236px;text-align:center;font-size:13px;color:var(--ink)}
</style>
</head>
<body>

<header class="site-header">
  <a class="brand" href="#"><span class="brand-mark"></span><span class="brand-name">MPTR</span></a>
  <nav class="main-nav">
    <a class="is-active" href="#" style="left:227px">MPTR</a>
    <a href="#" style="left:319px">FINANCIAL SERVICE</a>
    <a href="#" style="left:493px">NEWS</a>
    <a href="#" style="left:574px">MARKET TOOLS</a>
    <a href="#" style="left:726px">FORMS</a>
    <a href="#" style="left:816px">CAREERS</a>
    <a class="login" href="#" style="left:900px">LOGIN</a>
  </nav>
  <div class="lang"><span class="lang-dot"></span>ENGLISH
    <svg width="10" height="10" viewBox="0 0 10 10"><path d="M2 3l3 3 3-3" fill="none" stroke="#2b2b2b" stroke-width="1.4"/></svg>
  </div>
</header>

<section class="hero" role="img" aria-label="Aerial photograph of a waterfront city skyline with towers and a bay">
  <svg class="hero-arrow" style="left:54px" viewBox="0 0 14 14"><path d="M9 2L4 7l5 5" fill="none" stroke="#fff" stroke-width="2"/></svg>
  <div class="hero-copy">
    <h1 class="hero-title">MPTR</h1>
    <p class="hero-sub">We are a Financial Services</p>
  </div>
  <svg class="hero-arrow" style="left:1134px" viewBox="0 0 14 14"><path d="M5 2l5 5-5 5" fill="none" stroke="#fff" stroke-width="2"/></svg>
</section>

<section class="who">
  <div class="abs placeholder" role="img" aria-label="Laptop, smartphone and cup of coffee on a white desk"
       style="left:78px;top:40px;width:462px;height:390px;background:linear-gradient(150deg,#e4e4e4 0%,#d2d2d2 45%,#ececec 100%)"></div>
  <div class="abs" style="left:587px;top:108px;width:525px">
    <h2 class="section-title">WHO WE ARE</h2>
    <p class="copy" style="margin-top:14px">It is a long established fact that a reader will be distracted by the readable content of a page when looking at its layout. The point of using Lorem Ipsum is that it has a more-or-less normal distribution of letters, as opposed to using 'Content here, content here', making it look like readable English. Many desktop publishing packages and web page editors now use Lorem Ipsum as their default model text, and a search for 'lorem ipsum' will uncover many web sites still in their infancy. Various versions have evolved over the years, sometimes by accident, sometimes on purpose</p>
    <a class="btn-outline" href="#">ABOUT MPTR &#9656;</a>
  </div>
</section>

<section class="what">
  <div class="abs" style="left:88px;top:96px;width:596px">
    <h2 class="section-title">WHAT WE DO</h2>
    <p class="copy" style="margin-top:14px">It is a long established fact that a reader will be distracted by the readable content of a page when looking at its layout. The point of using Lorem Ipsum is that it has a more-or-less normal distribution of letters, as opposed to using 'Content here, content here', making it look like readable English. Many desktop publishing packages and web page editors now use Lorem Ipsum as their default model text, and a search for 'lorem ipsum' will uncover many web sites still in their infancy. Various versions have evolved over the years, sometimes by accident, sometimes on purpose</p>
    <a class="btn-outline" href="#">READ MORE &#9656;</a>
  </div>
  <div class="abs placeholder" role="img" aria-label="Illustration of a monitor and tablet showing growth charts, with a magnifying glass, cloud and gears"
       style="left:769px;top:50px;width:328px;height:300px;background:linear-gradient(135deg,#bfe0d8 0%,#2f5f8a 45%,#f0a040 100%)"></div>
</section>

<h2 class="section-title news-title">LATEST NEWS</h2>
<article class="news-card" style="left:88px">
  <div class="photo placeholder" role="img" aria-label="Person reviewing printed charts beside a laptop" style="background:linear-gradient(135deg,#c9a48a,#e8e3e4 60%,#f5f1ea)"></div>
  <h3>Neque porro quisquam est qui</h3><time>19/11/17</time>
</article>
<article class="news-card" style="left:439px">
  <div class="photo placeholder" role="img" aria-label="Businessman watering a plant shaped like a rising arrow" style="background:linear-gradient(180deg,#bfc3c4,#8e9394 70%,#6f7a5a)"></div>
  <h3>Dolorem ipsum quia dolor sit amet</h3><time>17/11/17</time>
</article>
<article class="news-card" style="left:789px">
  <div class="photo placeholder" role="img" aria-label="Businessman using a phone in front of city buildings" style="background:linear-gradient(90deg,#dfe6ee,#b7c3cf 60%,#4a5460)"></div>
  <h3>Quisquam est qui dolorem</h3><time>13/11/17</time>
</article>

<div class="partners" aria-label="Partners">
  <span class="partner"></span><span class="partner"></span><span class="partner"></span>
  <span class="partner"></span><span class="partner"></span><span class="partner"></span>
</div>

<section class="market">
  <h2 class="section-title">MARKET TOOL</h2>
  <div class="tool-card" style="left:88px">
    <h3>MOST ACTIVE COMPANY</h3>
    <ul>
      <li><svg width="10" height="10" viewBox="0 0 10 10"><circle cx="5" cy="5" r="5" fill="#2b2b2b"/><path d="M4 3l2 2-2 2" fill="none" stroke="#fff" stroke-width="1.3"/></svg>Neque porro quisquam qui</li>
      <li><svg width="10" height="10" viewBox="0 0 10 10"><circle cx="5" cy="5" r="5" fill="#2b2b2b"/><path d="M4 3l2 2-2 2" fill="none" stroke="#fff" stroke-width="1.3"/></svg>Quisquam est qui dolorem</li>
      <li><svg width="10" height="10" viewBox="0 0 10 10"><circle cx="5" cy="5" r="5" fill="#2b2b2b"/><path d="M4 3l2 2-2 2" fill="none" stroke="#fff" stroke-width="1.3"/></svg>Porro quisquam est qui dolorem</li>
      <li><svg width="10" height="10" viewBox="0 0 10 10"><circle cx="5" cy="5" r="5" fill="#2b2b2b"/><path d="M4 3l2 2-2 2" fill="none" stroke="#fff" stroke-width="1.3"/></svg>Dolorem ipsum quia dolor sit</li>
      <li><svg width="10" height="10" viewBox="0 0 10 10"><circle cx="5" cy="5" r="5" fill="#2b2b2b"/><path d="M4 3l2 2-2 2" fill="none" stroke="#fff" stroke-width="1.3"/></svg>Neque porro quisquam dolorem</li>
      <li><svg width="10" height="10" viewBox="0 0 10 10"><circle cx="5" cy="5" r="5" fill="#2b2b2b"/><path d="M4 3l2 2-2 2" fill="none" stroke="#fff" stroke-width="1.3"/></svg>Ipsum quia dolor sit amet</li>
      <li><svg width="10" height="10" viewBox="0 0 10 10"><circle cx="5" cy="5" r="5" fill="#2b2b2b"/><path d="M4 3l2 2-2 2" fill="none" stroke="#fff" stroke-width="1.3"/></svg>Quisquam est qui dolorem ipsum</li>
    </ul>
  </div>
  <div class="tool-card" style="left:439px">
    <h3>TOP GAINER</h3>
    <ul>
      <li><svg width="10" height="10" viewBox="0 0 10 10"><circle cx="5" cy="5" r="5" fill="#2b2b2b"/><path d="M4 3l2 2-2 2" fill="none" stroke="#fff" stroke-width="1.3"/></svg>Neque porro quisquam qui</li>
      <li><svg width="10" height="10" viewBox="0 0 10 10"><circle cx="5" cy="5" r="5" fill="#2b2b2b"/><path d="M4 3l2 2-2 2" fill="none" stroke="#fff" stroke-width="1.3"/></svg>Quisquam est qui dolorem</li>
      <li><svg width="10" height="10" viewBox="0 0 10 10"><circle cx="5" cy="5" r="5" fill="#2b2b2b"/><path d="M4 3l2 2-2 2" fill="none" stroke="#fff" stroke-width="1.3"/></svg>Porro quisquam est qui dolorem</li>
      <li><svg width="10" height="10" viewBox="0 0 10 10"><circle cx="5" cy="5" r="5" fill="#2b2b2b"/><path d="M4 3l2 2-2 2" fill="none" stroke="#fff" stroke-width="1.3"/></svg>Dolorem ipsum quia dolor sit</li>
      <li><svg width="10" height="10" viewBox="0 0 10 10"><circle cx="5" cy="5" r="5" fill="#2b2b2b"/><path d="M4 3l2 2-2 2" fill="none" stroke="#fff" stroke-width="1.3"/></svg>Neque porro quisquam dolorem</li>
      <li><svg width="10" height="10" viewBox="0 0 10 10"><circle cx="5" cy="5" r="5" fill="#2b2b2b"/><path d="M4 3l2 2-2 2" fill="none" stroke="#fff" stroke-width="1.3"/></svg>Ipsum quia dolor sit amet</li>
      <li><svg width="10" height="10" viewBox="0 0 10 10"><circle cx="5" cy="5" r="5" fill="#2b2b2b"/><path d="M4 3l2 2-2 2" fill="none" stroke="#fff" stroke-width="1.3"/></svg>Quisquam est qui dolorem ipsum</li>
    </ul>
  </div>
  <div class="tool-card" style="left:784px">
    <h3>TOP LOSER</h3>
    <ul>
      <li><svg width="10" height="10" viewBox="0 0 10 10"><circle cx="5" cy="5" r="5" fill="#2b2b2b"/><path d="M4 3l2 2-2 2" fill="none" stroke="#fff" stroke-width="1.3"/></svg>Neque porro quisquam qui</li>
      <li><svg width="10" height="10" viewBox="0 0 10 10"><circle cx="5" cy="5" r="5" fill="#2b2b2b"/><path d="M4 3l2 2-2 2" fill="none" stroke="#fff" stroke-width="1.3"/></svg>Quisquam est qui dolorem</li>
      <li><svg width="10" height="10" viewBox="0 0 10 10"><circle cx="5" cy="5" r="5" fill="#2b2b2b"/><path d="M4 3l2 2-2 2" fill="none" stroke="#fff" stroke-width="1.3"/></svg>Porro quisquam est qui dolorem</li>
      <li><svg width="10" height="10" viewBox="0 0 10 10"><circle cx="5" cy="5" r="5" fill="#2b2b2b"/><path d="M4 3l2 2-2 2" fill="none" stroke="#fff" stroke-width="1.3"/></svg>Dolorem ipsum quia dolor sit</li>
      <li><svg width="10" height="10" viewBox="0 0 10 10"><circle cx="5" cy="5" r="5" fill="#2b2b2b"/><path d="M4 3l2 2-2 2" fill="none" stroke="#fff" stroke-width="1.3"/></svg>Neque porro quisquam dolorem</li>
      <li><svg width="10" height="10" viewBox="0 0 10 10"><circle cx="5" cy="5" r="5" fill="#2b2b2b"/><path d="M4 3l2 2-2 2" fill="none" stroke="#fff" stroke-width="1.3"/></svg>Ipsum quia dolor sit amet</li>
      <li><svg width="10" height="10" viewBox="0 0 10 10"><circle cx="5" cy="5" r="5" fill="#2b2b2b"/><path d="M4 3l2 2-2 2" fill="none" stroke="#fff" stroke-width="1.3"/></svg>Quisquam est qui dolorem ipsum</li>
    </ul>
  </div>
</section>

<footer class="site-footer">
  <a class="foot-brand" href="#"><span class="brand-mark"></span><span class="brand-name" style="font-size:24px">MPTR</span></a>
  <div class="foot-col" style="left:315px">
    <h4>CONTACT US</h4>
    <p>Address : 12 Harbour Lane, West Quay,<br>Doha 4410<br>Phone : +974 4 5550182<br>Email : info@mptr-example.com</p>
  </div>
  <div class="foot-col" style="left:637px;width:220px">
    <h4>JOIN OUR MAILING LIST</h4>
    <p>Your about us information would fit here nicely.</p>
    <div class="mail-form"><span>Email address</span><b>Submit</b></div>
  </div>
  <div class="foot-col" style="left:938px">
    <h4>FOLLOW US OUT THERE</h4>
    <div class="socials"><span></span><span></span><span></span><span></span></div>
  </div>
  <div class="foot-rule"></div>
  <p class="copyright">Copyright © 2017. All Rights Reserved</p>
</footer>

</body>
</html>
```